KRV Photography Business Card Design

I would like a business card designed in the shape of a camera.
Would like to see various camera designs. Would like to see what the card looks like in different colors. Would like to see which logo looks better on the various camera designs so please show me some with the white logo and some with the black logo. If you need a different file formats please let me know.
Project Deadline Extended Reason: My grandfather passed away and dealing with funeral plans so need to extend deadline. Added Tuesday, March 1, 2016
Project Deadline Extended
Reason: I just got back from out of town. My grandfather's passing was the primary focus for me these past few weeks and the funeral is over so now I will concentrate on picking my business card design. I really appreciate each designer who has taken the time to submit a design. Your effort has not gone unnoticed. I look forward to seeing more amazing designs.
Business
Contact Information for Business Card
Dorine
555-418-2706
https://www.facebook.com/krvphotographyfreelance/
MonaDorine@krv-photography.example

```html
<!DOCTYPE html>
<html lang="en">
<head>
<meta charset="utf-8">
<title>KRV Photography – Camera Business Cards</title>
<link rel="stylesheet" href="https://fonts.googleapis.com/css2?family=Cinzel:wght@400&family=Open+Sans:wght@400;600;700&display=swap">
<style>
  :root {
    --backdrop: #bcbdbf;
    --card-black: #000000;
    --accent-gold: #c4812f;
    --logo-gold: #d6a43a;
    --plain-white: #ffffff;
  }
  html, body {
    margin: 0;
    padding: 0;
    width: 1200px;
    height: 927px;
    overflow: hidden;
    background: var(--backdrop);
  }
  .canvas { display: block; width: 1200px; height: 927px; }
  .card-body { fill: var(--card-black); }
  .brand-mark { fill: var(--logo-gold); }
  .brand-name {
    font-family: "Cinzel", serif;
    font-weight: 400;
    font-size: 18px;
    fill: var(--logo-gold);
  }
  .holder-name {
    font-family: "Open Sans", sans-serif;
    font-weight: 700;
    font-size: 25px;
    letter-spacing: 1.6px;
  }
  .contact-line {
    font-family: "Open Sans", sans-serif;
    font-weight: 400;
    font-size: 14.5px;
    letter-spacing: 0.8px;
  }
  .icon { fill: none; stroke-width: 1.2; stroke-linecap: round; stroke-linejoin: round; }
  .card--gold .accent-stripe { fill: var(--accent-gold); }
  .card--gold .holder-name, .card--gold .contact-line { fill: var(--accent-gold); }
  .card--gold .icon { stroke: var(--accent-gold); }
  .card--white .accent-stripe { fill: var(--plain-white); }
  .card--white .holder-name, .card--white .contact-line { fill: var(--plain-white); }
  .card--white .icon { stroke: var(--plain-white); }
</style>
</head>
<body>
<svg class="canvas" viewBox="0 0 1200 927" xmlns="http://www.w3.org/2000/svg">
  <defs>
    <g id="camera-shape">
      <rect class="card-body" x="71" y="-5" width="62" height="30" rx="6"/>
      <rect class="card-body" x="375" y="-23" width="102" height="40" rx="9"/>
      <rect class="card-body" x="0" y="0" width="531" height="368" rx="22"/>
    </g>
  </defs>

  <g class="card card--gold" transform="translate(47 291)">
    <use href="#camera-shape"/>
    <rect class="accent-stripe" x="28" y="0" width="39" height="368"/>
    <circle class="brand-mark" cx="404" cy="60" r="32"/>
    <text class="brand-name" x="501" y="120" text-anchor="end">KRV PHOTOGRAPHY</text>
    <text class="holder-name" x="81" y="289">THEO MARSDEN</text>
    <path class="icon" d="M83 307 l3 -1 l2 4 l-2 1 q1 3 4 5 l1 -2 l4 2 l-1 3 q-8 -1 -11 -12z"/>
    <text class="contact-line" x="107" y="318">+330 2555-0148</text>
    <rect class="icon" x="81" y="328" width="11" height="8" rx="1"/>
    <path class="icon" d="M81 329 l5.5 4 l5.5 -4"/>
    <text class="contact-line" x="107" y="336">theo@marsdenstudio.example</text>
  </g>

  <g class="card card--white" transform="translate(620 291)">
    <use href="#camera-shape"/>
    <rect class="accent-stripe" x="28" y="0" width="39" height="368"/>
    <circle class="brand-mark" cx="404" cy="60" r="32"/>
    <text class="brand-name" x="501" y="120" text-anchor="end">KRV PHOTOGRAPHY</text>
    <text class="holder-name" x="81" y="289">THEO MARSDEN</text>
    <path class="icon" d="M83 307 l3 -1 l2 4 l-2 1 q1 3 4 5 l1 -2 l4 2 l-1 3 q-8 -1 -11 -12z"/>
    <text class="contact-line" x="107" y="318">+330 2555-0148</text>
    <rect class="icon" x="81" y="328" width="11" height="8" rx="1"/>
    <path class="icon" d="M81 329 l5.5 4 l5.5 -4"/>
    <text class="contact-line" x="107" y="336">theo@marsdenstudio.example</text>
  </g>
</svg>
</body>
</html>
```